Business Card Design for Property Development Company Director

I am looking for a professional and unforgettable business card design for our Director of our Property Development Company.
Please see attached .pptx file to find out what information to include. You don't have to follow the exact format shown in the file - I am interested to see your creative flair using the information provided.

```html
<!DOCTYPE html>
<html lang="en">
<head>
<meta charset="UTF-8">
<title>Norvane Property Group – Business Card</title>
<link rel="stylesheet" href="https://fonts.googleapis.com/css2?family=Lato:wght@300;400;700&display=swap">
<style>
  :root {
    --stage: #1c1c1c;
    --card: #121212;
    --card-edge: #1f1f1f;
    --text-light: #d9d9d9;
    --text-muted: #8a8a8a;
    --accent: #1a6fc9;
    --rule: #3a3a3a;
  }
  * { margin: 0; padding: 0; box-sizing: border-box; }
  html, body {
    width: 1200px; height: 900px; overflow: hidden;
    background: var(--stage);
    font-family: "Lato", Arial, sans-serif;
  }
  .stage {
    width: 1200px; height: 900px;
    display: flex; flex-direction: column;
    align-items: center; justify-content: center; gap: 44px;
  }
  .card {
    position: relative;
    width: 600px; height: 343px;
    background: var(--card);
    border: 1px solid var(--card-edge);
    border-radius: 20px;
    box-shadow: 0 18px 40px rgba(0,0,0,0.55);
    overflow: hidden;
  }

  /* Front */
  .card-front { text-align: center; color: var(--text-light); }
  .front-tagline {
    position: absolute; top: 44px; left: 0; right: 0;
    font-size: 13px; font-weight: 400; letter-spacing: 0.4px; line-height: 1.35;
  }
  .front-brand {
    position: absolute; top: 128px; left: 0; right: 0;
    display: flex; align-items: center; justify-content: center; gap: 14px;
    font-size: 40px; font-weight: 700; letter-spacing: 3px; color: var(--text-light);
  }
  .brand-square { width: 26px; height: 26px; background: var(--text-light); }
  .front-rule {
    position: absolute; top: 228px; left: 70px; right: 70px;
    height: 1px; background: var(--rule);
  }
  .front-invite {
    position: absolute; bottom: 42px; left: 0; right: 0;
    font-size: 14px; font-weight: 400;
  }

  /* Back */
  .card-back { color: var(--text-light); }
  .back-brand {
    position: absolute; top: 54px; right: 60px;
    display: flex; align-items: center; gap: 12px;
    font-size: 30px; font-weight: 700; letter-spacing: 2px; color: var(--accent);
  }
  .back-brand .brand-square { width: 20px; height: 20px; background: var(--accent); }
  .back-rule {
    position: absolute; top: 130px; left: 170px; right: 40px;
    height: 1px; background: var(--rule);
  }
  .holder { position: absolute; left: 40px; top: 176px; }
  .holder-name {
    font-size: 21px; font-weight: 700; color: var(--accent); letter-spacing: 0.5px;
  }
  .holder-title { font-size: 15px; font-weight: 400; color: var(--text-muted); margin-top: 2px; }
  .holder-rule {
    position: absolute; left: 150px; top: 210px; right: 40px;
    height: 1px; background: var(--rule);
  }
  .contact-list { position: absolute; left: 40px; bottom: 34px; list-style: none; }
  .contact-list li {
    display: flex; align-items: center; gap: 10px;
    font-size: 16px; font-weight: 300; line-height: 1.5; color: var(--text-light);
  }
  .contact-list svg { width: 14px; height: 14px; fill: var(--accent); flex: none; }
  .licence {
    position: absolute; right: 40px; bottom: 96px;
    font-size: 13px; font-weight: 400; color: var(--text-muted);
  }
</style>
</head>
<body>
<main class="stage">

  <section class="card card-front" aria-label="Card front">
    <p class="front-tagline">PROPERTY DEVELOPMENT<br>&amp; SITE ACQUISITION SPECIALISTS</p>
    <div class="front-brand"><span class="brand-square"></span>NORVANE</div>
    <div class="front-rule"></div>
    <p class="front-invite">Ask me about our INVESTMENT &amp; PARTNERSHIP opportunities</p>
  </section>

  <section class="card card-back" aria-label="Card back">
    <div class="back-brand"><span class="brand-square"></span>NORVANE PROPERTY GROUP</div>
    <div class="back-rule"></div>

    <div class="holder">
      <p class="holder-name">DANIEL ASHWORTH</p>
      <p class="holder-title">Director</p>
    </div>
    <div class="holder-rule"></div>

    <p class="licence">Real Estate Lic: 5172036 &amp; 5172037</p>

    <ul class="contact-list">
      <li>
        <svg viewBox="0 0 24 24" aria-hidden="true"><path d="M6.6 10.8a15.1 15.1 0 0 0 6.6 6.6l2.2-2.2c.3-.3.7-.4 1-.2 1.1.4 2.3.6 3.6.6.6 0 1 .4 1 1V20c0 .6-.4 1-1 1A17 17 0 0 1 3 4c0-.6.4-1 1-1h3.5c.6 0 1 .4 1 1 0 1.3.2 2.5.6 3.6.1.3 0 .7-.2 1l-2.3 2.2z"/></svg>
        0400 318 627
      </li>
      <li>
        <svg viewBox="0 0 24 24" aria-hidden="true"><path d="M2 5h20v14H2zm2 2v.5l8 5 8-5V7l-8 5z"/></svg>
        daniel@norvane.com.au
      </li>
      <li>
        <svg viewBox="0 0 24 24" aria-hidden="true"><circle cx="12" cy="12" r="10"/></svg>
        www.norvane.com.au
      </li>
    </ul>
  </section>

</main>
</body>
</html>
```